New Business Card for our Indoor Golf Training Facility

We are looking for designs for a new business card for our indoor golf training facility. Attached is our logo, our logo with our slogan, and here is our elevator pitch (What makes us different from the others) not sure if all the info will fit on one card, maybe you can condense the elevator pitch? here is the info

Elevator Pitch
We work with serious golfers and those that want to be serious golfers…
to make you better, faster, at all phases of the game…
We use the same state-of-the-art technology as professional golfers…
which produces data sets that shows your improvement in real time.
Our facility is available 24/7 to our members, which allows you to improve on your time.

our website: www.birchpinlinks.com

Target Market(s)

Golfers

Font styles to use
Serif
Sans Serif

Colors
ec1f27
f59195
fbd4d5
919191
d3d3d3
1b1b1b

Requirements
Must have
• our logo or our logo with the slogan, elevator pitch (can be condensed or shortened)

```html
<!DOCTYPE html>
<html lang="en">
<head>
<meta charset="utf-8">
<title>Birch Pin Links — Business Card</title>
<link rel="stylesheet" href="https://fonts.googleapis.com/css2?family=Roboto:wght@400;500;700;900&display=swap">
<style>
  :root {
    --brand-red: #ec1f27;
    --pitch-red: #e33a36;
    --soft-pink: #fbd4d5;
    --ink: #1b1b1b;
    --grey: #555555;
    --card-white: #f7f7f7;
    --backdrop: #d3d3d3;
  }
  * { box-sizing: border-box; margin: 0; padding: 0; }
  html, body { width: 1200px; height: 911px; overflow: hidden; }
  body {
    background: var(--backdrop);
    font-family: "Roboto", Arial, sans-serif;
    color: var(--ink);
    position: relative;
  }
  .card {
    position: absolute;
    top: 170px;
    width: 340px;
    height: 570px;
    background: var(--card-white);
    border-radius: 22px;
    overflow: hidden;
    box-shadow: 0 6px 18px rgba(0,0,0,0.25);
  }
  .card--front { left: 190px; }
  .card--back { left: 670px; }

  /* Front */
  .contact {
    position: absolute;
    left: 34px;
    bottom: 70px;
    right: 24px;
  }
  .contact__name {
    color: var(--brand-red);
    font-weight: 700;
    font-size: 25px;
    line-height: 1.1;
  }
  .contact__title {
    font-weight: 700;
    font-size: 15px;
    margin-bottom: 16px;
  }
  .contact__address {
    font-size: 15px;
    color: var(--grey);
    line-height: 1.35;
    margin-bottom: 10px;
  }
  .contact__line {
    font-size: 15px;
    color: var(--grey);
    line-height: 1.4;
  }
  .contact__label { color: var(--brand-red); font-weight: 700; }

  /* Back */
  .brand {
    position: absolute;
    top: 48px;
    left: 30px;
    right: 20px;
    display: flex;
    align-items: center;
    gap: 10px;
  }
  .brand__dot {
    width: 38px; height: 38px;
    border-radius: 50%;
    background: var(--brand-red);
    flex: none;
  }
  .brand__name {
    color: var(--brand-red);
    font-weight: 900;
    font-size: 34px;
    line-height: 1;
  }
  .brand__slogan {
    position: absolute;
    top: 92px;
    left: 78px;
    color: var(--brand-red);
    font-size: 12px;
    letter-spacing: 0.2px;
  }
  .pitch {
    position: absolute;
    left: 0; right: 0;
    top: 250px;
    height: 272px;
    background: var(--pitch-red);
    color: #ffffff;
    text-align: center;
  }
  .pitch__tab {
    position: absolute;
    top: -2px;
    left: 50%;
    transform: translateX(-50%);
    background: var(--pitch-red);
    border: 2px solid #ffffff;
    border-top: none;
    border-radius: 0 0 14px 14px;
    padding: 8px 18px;
    font-weight: 700;
    font-size: 17px;
    letter-spacing: 0.5px;
    white-space: nowrap;
  }
  .pitch__text {
    padding: 50px 20px 0;
    font-size: 12.5px;
    line-height: 1.45;
  }
  .pitch__social {
    display: flex;
    justify-content: center;
    gap: 6px;
    margin-top: 10px;
  }
  .pitch__social span {
    width: 16px; height: 16px;
    border-radius: 50%;
    border: 2px solid #ffffff;
  }
</style>
</head>
<body>
  <section class="card card--front" aria-label="Card front">
    <div class="contact">
      <p class="contact__name">Dana Whitfield</p>
      <p class="contact__title">CEO/Founder</p>
      <p class="contact__address">418 Meadow Crest Ave. Suite B4<br>Fairbrook, OH 45890</p>
      <p class="contact__line"><span class="contact__label">Phone:</span> 555-210-3388</p>
      <p class="contact__line"><span class="contact__label">Email:</span> info@birchpinlinks.com</p>
      <p class="contact__line"><span class="contact__label">Web:</span> www.birchpinlinks.com</p>
    </div>
  </section>

  <section class="card card--back" aria-label="Card back">
    <div class="brand">
      <span class="brand__dot"></span>
      <span class="brand__name">Birch Pin Links</span>
    </div>
    <p class="brand__slogan">Play Well. Practice Smart. Go Further.</p>

    <div class="pitch">
      <div class="pitch__tab">ELEVATOR PITCH :</div>
      <p class="pitch__text">
        We coach dedicated players and anyone<br>
        ready to take the game seriously…<br>
        to help you improve,<br>
        quicker, in every part of your game…<br>
        Our bays run the same launch-monitor systems<br>
        the touring pros rely on…<br>
        giving you clear numbers that track your<br>
        progress shot by shot.<br>
        Members can train any hour, any day,<br>
        so practice fits around your schedule.
      </p>
      <div class="pitch__social" aria-label="Social links">
        <span></span><span></span>
      </div>
    </div>
  </section>
</body>
</html>
```